Website for IT consulting Company

I need a website upgrade, the existing site content is ok, I would also like to add a testimonial page, the site should be something that is easy for us to update content. You use the content from www.kelvanbrook.com as an example. I will also post update logo and artwork. I also need a contact form with some type of validation or captcha.

I added Coded to the Project

Please omit Address maps

Target Market(s)

small business, service oriented companies. We provide IT Consulting, support and mangement

Industry/Entity Type

Information Technology

Coding

Number of Pages Required

1 page

Font styles to use
Serif
Sans Serif

Requirements
Must have
• Contain logo attached, and content from existing web site www.kelvanbrook.com.
• Also need to update content easily, and be movable to different platforms.
• There is a catch phrase
• "Let us worry about your technology…” “ so you don’t have to!”
• Should be included.
Nice to have
• Testimonial page, Project page where we can post new and past projects and pictures
Should not have
• none

```html
<!DOCTYPE html>
<html lang="en">
<head>
<meta charset="utf-8">
<title>Kelvanbrook — IT Solutions</title>
<link rel="stylesheet" href="https://fonts.googleapis.com/css2?family=Open+Sans:wght@400;600;700;800&family=PT+Serif:ital@0;1&display=swap">
<style>
:root{
  --orange:#f07f27;
  --orange-dark:#e06c14;
  --navy:#1b202c;
  --hero-a:#0d1a2c;
  --hero-b:#3c5878;
  --ink:#2b2b2b;
  --muted:#555;
  --soft:#8a8a8a;
  --panel:#efefef;
  --news:#f3f3f3;
  --footer:#3d3d3d;
  --white:#fff;
}
*{box-sizing:border-box;margin:0;padding:0}
html,body{width:1200px;height:3830px;overflow:hidden}
body{font-family:"Open Sans",Arial,sans-serif;color:var(--ink);background:var(--white);position:relative}
section,header,footer,nav{position:absolute;left:0;width:1200px}
.btn{display:inline-block;border:2px solid var(--orange);border-radius:4px;color:var(--ink);font-size:15px;font-weight:600;text-align:center;background:var(--white)}

/* header */
.topbar{top:0;height:115px;background:var(--navy)}
.brand{position:absolute;left:100px;top:30px;display:flex;align-items:center;gap:14px}
.brand-mark{width:44px;height:44px;background:var(--orange);border-radius:4px}
.brand-name{font-size:40px;font-weight:700;color:var(--white);letter-spacing:1px}
.contact-top{position:absolute;right:100px;top:40px;display:flex;gap:40px;color:var(--white);font-size:17px;font-weight:600;align-items:center}
.contact-top span{display:flex;align-items:center;gap:12px}
.contact-top .phone{font-size:20px;font-weight:700}

/* hero */
.hero{top:115px;height:447px;background:linear-gradient(100deg,var(--hero-a) 0%,#1a2c44 45%,var(--hero-b) 75%,#203249 100%)}
.hero-photo{position:absolute;right:0;top:0;width:640px;height:447px;background:radial-gradient(ellipse at 55% 35%,#9fb3c8 0%,#4a6686 35%,rgba(20,35,55,0) 75%)}
.hero-copy{position:absolute;left:102px;top:115px;color:var(--white)}
.hero-copy h1{font-size:32px;font-weight:700;line-height:40px;text-transform:uppercase}
.hero-copy h1 b{font-size:38px;font-weight:800}
.hero-copy p{font-size:23px;margin-top:4px;text-transform:uppercase}
.hero-copy .btn{margin-top:30px;width:155px;height:46px;line-height:42px;background:transparent;color:var(--white);border-color:var(--orange)}
.dots{position:absolute;left:560px;top:396px;display:flex;gap:10px}
.dots i{width:13px;height:13px;border-radius:50%;background:var(--white)}
.dots i:first-child{background:var(--orange)}

/* nav */
.mainnav{top:562px;height:35px;background:var(--orange);display:flex;align-items:center}
.mainnav ul{list-style:none;display:flex;gap:42px;margin-left:112px}
.mainnav a{color:var(--white);text-decoration:none;font-size:15px;font-weight:700;text-transform:uppercase}
.social-top{position:absolute;right:102px;top:7px;display:flex;gap:8px}
.social-top i{width:22px;height:22px;border:2px solid var(--white);border-radius:50%}

/* services */
.services{top:597px;height:343px;display:flex;gap:58px;padding:70px 0 0 97px}
.service{width:300px}
.service-head{display:flex;align-items:center;gap:12px;height:42px}
.service-icon{width:34px;height:34px;border-radius:50%;background:var(--orange);flex:none}
.service h3{font-size:14px;font-weight:700;text-transform:uppercase}
.service p{font-size:14.5px;line-height:22.5px;color:var(--muted);margin-top:12px;height:92px}
.more{display:flex;align-items:center;gap:8px;font-size:14px;font-weight:600;color:var(--ink);margin-top:18px}

/* welcome */
.welcome{top:940px;height:357px;background:var(--orange);text-align:center;color:var(--white)}
.welcome h2{font-size:27px;font-weight:700;letter-spacing:2px;margin-top:62px;text-transform:uppercase}
.welcome p{width:1010px;margin:22px auto 0;font-size:15.5px;line-height:29px;text-align:left}
.welcome .btn{margin-top:22px;width:155px;height:48px;line-height:44px;background:transparent;color:var(--white);border-color:var(--white)}

/* support diagram */
.support{top:1297px;height:640px}
.support svg{position:absolute;left:0;top:0}
.node{position:absolute;font-size:11.5px;line-height:15px;color:var(--soft);width:250px}
.node h4{font-size:14px;font-weight:600;color:var(--ink);text-transform:uppercase}
.node.hl h4{color:var(--orange)}
.node .ico{display:block;width:34px;height:34px;border-radius:6px;background:var(--ink);margin-bottom:6px}
.node.hl .ico{background:var(--orange)}
.hub{position:absolute;left:450px;top:300px;width:300px;text-align:center}
.hub b{display:block;font-size:31px;font-weight:800}
.hub span{font-size:15px;font-weight:600;letter-spacing:1px}

/* flexible */
.flex-panel{top:1953px;left:475px;width:674px;height:396px;background:var(--panel)}
.flex-photo{top:1979px;left:97px;width:505px;height:349px;background:linear-gradient(90deg,#c9cdd2 0%,#e8eaec 40%,#6f7882 70%,#2d333b 100%)}
.flex-copy{position:absolute;left:175px;top:24px;width:460px}
.flex-copy h2{font-size:28px;font-weight:700;line-height:34px;text-transform:uppercase}
.flex-copy p{font-size:14.5px;line-height:26px;color:var(--ink);margin-top:14px}
.flex-copy ul{list-style:none;display:flex;gap:44px;font-size:13px;margin-top:8px;text-transform:uppercase}
.flex-copy .btn{margin-top:14px;width:150px;height:46px;line-height:42px}

/* quote */
.quote{top:2400px;height:350px;background:var(--orange)}
.quote-photo{position:absolute;left:0;top:0;width:1200px;height:350px;background:linear-gradient(90deg,#8a98a6 0%,#d7dde3 50%,#9aa4ae 100%);clip-path:polygon(528px 0,1200px 0,1200px 350px,740px 350px)}
.quote-text{position:absolute;left:70px;top:110px;width:450px;text-align:center;color:var(--white);font-size:28px;font-weight:700;line-height:34px;text-transform:uppercase}

/* testimonials */
.testimonials{top:2750px;height:543px;text-align:center}
.testimonials h2{font-size:27px;font-weight:700;margin-top:58px;text-transform:uppercase}
.t-row{position:absolute;top:115px;left:0;width:1200px}
.t-card{position:absolute;width:330px;text-align:center}
.t-avatar{width:192px;height:192px;border-radius:50%;border:8px solid #e6e6e6;background:linear-gradient(160deg,#9a9a9a,#3a3a3a);margin:0 auto}
.t-card h3{font-size:20px;font-weight:400;margin-top:22px;text-transform:uppercase}
.t-card h3 b{font-weight:700}
.t-card p{font-family:"PT Serif",Georgia,serif;font-size:14.5px;line-height:22px;margin-top:4px}
.t-card .role{color:#1a7ad1;font-weight:600;font-size:14.5px;margin-top:4px}
.t-card .more{justify-content:center;margin-top:6px}

/* newsletter */
.newsletter{top:3293px;height:179px;background:var(--news);text-align:center}
.newsletter h2{font-size:23px;font-weight:700;margin-top:36px;letter-spacing:1px;text-transform:uppercase}
.newsletter h3{font-size:13px;font-weight:600;letter-spacing:1px;text-transform:uppercase}
.news-form{display:flex;justify-content:center;margin-top:20px}
.news-form span{width:415px;height:24px;border:1px solid #d0d0d0;background:var(--white);font-size:10px;color:var(--soft);text-align:left;padding:4px 8px}
.news-form b{width:96px;height:24px;background:var(--orange);color:var(--white);font-size:13px;line-height:24px;text-transform:uppercase}

/* footer */
.site-footer{top:3472px;height:291px;background:var(--footer);color:var(--white);text-align:center}
.site-footer h2{font-size:23px;font-weight:700;margin-top:32px;text-transform:uppercase}
.foot-links{font-size:13px;font-weight:700;margin-top:6px;text-transform:uppercase;word-spacing:4px}
.foot-contact{position:absolute;top:110px;left:205px;width:790px;display:flex;justify-content:space-between}
.foot-item{width:230px;display:flex;flex-direction:column;align-items:center;gap:18px;font-size:16px}
.foot-item i{width:61px;height:61px;border:2px solid var(--white);border-radius:50%;display:flex;align-items:center;justify-content:center}
.social-foot{position:absolute;top:235px;left:0;width:1200px;display:flex;justify-content:center;gap:14px}
.social-foot i{width:38px;height:38px;border:2px solid var(--white);border-radius:50%}
.copyright{top:3763px;height:67px;background:var(--orange);color:var(--white);text-align:center;font-size:16px;line-height:67px}
</style>
</head>
<body>

<header class="topbar">
  <div class="brand"><span class="brand-mark"></span><span class="brand-name">KELVANBROOK</span></div>
  <div class="contact-top">
    <span><svg width="20" height="26" viewBox="0 0 20 26"><path d="M10 0C4.5 0 0 4.4 0 9.8 0 17 10 26 10 26s10-9 10-16.2C20 4.4 15.5 0 10 0z" fill="#f07f27"/><circle cx="10" cy="9.5" r="3.6" fill="#1b202c"/></svg>123 Street, City Name, DC 12345</span>
    <span class="phone"><svg width="24" height="24" viewBox="0 0 24 24"><rect width="24" height="24" rx="3" fill="#f07f27"/><path d="M8 5l2.5 3.5-1.5 2c.8 1.8 2.3 3.3 4 4l2-1.5L18.5 16 17 18.5C11 18 6 13 5.5 7z" fill="#1b202c"/></svg>123-4567-8910</span>
  </div>
</header>

<section class="hero">
  <div class="hero-photo" role="img" aria-label="Photo of a businessman holding a tablet with a glowing cloud and network connections above it"></div>
  <div class="hero-copy">
    <h1>IT solutions that work for<br><b>your business.</b></h1>
    <p>A full service technology company</p>
    <a class="btn">Read More</a>
  </div>
  <div class="dots"><i></i><i></i><i></i><i></i></div>
</section>

<nav class="mainnav">
  <ul><li><a>Home</a></li><li><a>About</a></li><li><a>Contact</a></li><li><a>Support</a></li><li><a>Clients</a></li><li><a>Careers</a></li></ul>
  <div class="social-top"><i></i><i></i><i></i><i></i><i></i><i></i></div>
</nav>

<section class="services">
  <article class="service">
    <div class="service-head"><span class="service-icon"></span><h3>Managed IT Solutions</h3></div>
    <p>Our staff will design, service, administer and maintain your IT needs. We are well versed on all major operating system, and network appliances...</p>
    <a class="more">Read More... <svg width="20" height="20" viewBox="0 0 20 20"><circle cx="10" cy="10" r="8.5" fill="none" stroke="#f07f27" stroke-width="2"/><path d="M6 10h7M10 6.5l3.5 3.5-3.5 3.5" fill="none" stroke="#f07f27" stroke-width="2"/></svg></a>
  </article>
  <article class="service">
    <div class="service-head"><span class="service-icon"></span><h3>Remote Diagnostic &amp;Support</h3></div>
    <p>Do you need a quick solution to a technical problem? With our live remote-assistance tool, a member of our support team can view your desktop and share control ...</p>
    <a class="more">Read More... <svg width="20" height="20" viewBox="0 0 20 20"><circle cx="10" cy="10" r="8.5" fill="none" stroke="#f07f27" stroke-width="2"/><path d="M6 10h7M10 6.5l3.5 3.5-3.5 3.5" fill="none" stroke="#f07f27" stroke-width="2"/></svg></a>
  </article>
  <article class="service">
    <div class="service-head"><span class="service-icon"></span><h3>IT Infrastructure Design</h3></div>
    <p>Do you have more than one site? Do you need remote access? We can design and implement LANS/WANS and VPN's. Make your ...</p>
    <a class="more">Read More... <svg width="20" height="20" viewBox="0 0 20 20"><circle cx="10" cy="10" r="8.5" fill="none" stroke="#f07f27" stroke-width="2"/><path d="M6 10h7M10 6.5l3.5 3.5-3.5 3.5" fill="none" stroke="#f07f27" stroke-width="2"/></svg></a>
  </article>
</section>

<section class="welcome">
  <h2>Welcome to Kelvanbrook</h2>
  <p>Outsourcing is subcontracting a process, such as product design or manufacturing, to a third-party company.[1] The decision to outsource is often made in the interest of lowering firm costs, redirecting or conserving energy directed at the competencies of a particular business, or to make more efficient use of land, labor, capital, (information) technology and resources. Outsourcing became part of the business lexicon during the 1980s</p>
  <a class="btn">Read More</a>
</section>

<section class="support">
  <svg width="1200" height="640" viewBox="0 0 1200 640">
    <g fill="none" stroke-width="3" stroke="#2b2b2b">
      <path d="M600 164V112"/>
      <path d="M705 210L760 170H880"/>
      <path d="M752 300H830"/>
      <path d="M720 420L780 395H880"/>
      <path d="M600 474V505"/>
      <path d="M480 420L420 395H300"/>
      <path d="M448 330H360"/>
      <path d="M495 210L440 185H300"/>
    </g>
    <circle cx="600" cy="319" r="142" fill="none" stroke="#3a3a3a" stroke-width="26" stroke-dasharray="99.5 12" transform="rotate(-105 600 319)"/>
    <circle cx="600" cy="319" r="142" fill="none" stroke="#f07f27" stroke-width="26" stroke-dasharray="99.5 123.5" transform="rotate(-105 600 319)"/>
  </svg>
  <div class="hub"><b>IT SUPPORT</b><span>SOLUTIONS</span></div>
  <div class="node hl" style="left:500px;top:50px;text-align:center"><span class="ico" style="margin:0 auto 6px"></span><h4>Network Administration.</h4>Lorem ipsum dolor sit amet,<br>consectetur adipiscing elit, sed</div>
  <div class="node" style="left:870px;top:140px"><span class="ico"></span><h4>Desktop Support.</h4>Lorem ipsum dolor sit amet,<br>consectetur adipiscing elit, sed</div>
  <div class="node hl" style="left:830px;top:270px"><span class="ico"></span><h4>Network Cabling</h4>Lorem ipsum dolor sit amet,<br>consectetur adipiscing elit, sed</div>
  <div class="node" style="left:872px;top:395px"><span class="ico"></span><h4>Antivirus Solutions</h4>Lorem ipsum dolor sit amet,<br>consectetur adipiscing elit, sed</div>
  <div class="node hl" style="left:535px;top:505px"><span class="ico"></span><h4>Disaster Recovery</h4>Lorem ipsum dolor sit amet,<br>consectetur adipiscing elit, sed</div>
  <div class="node" style="left:168px;top:404px"><span class="ico" style="margin-left:80px"></span><h4>Telecommunications.</h4>Lorem ipsum dolor sit amet,<br>consectetur adipiscing elit, sed</div>
  <div class="node hl" style="left:188px;top:274px"><span class="ico" style="margin-left:70px"></span><h4>Web Design.</h4>Lorem ipsum dolor sit amet,<br>consectetur adipiscing elit, sed</div>
  <div class="node" style="left:118px;top:120px"><span class="ico" style="margin-left:100px"></span><h4>Network Security</h4>Lorem ipsum dolor sit amet,<br>consectetur adipiscing elit, sed</div>
</section>

<section class="flex-panel">
  <div class="flex-copy">
    <h2>Flexible solutions for your business needs</h2>
    <p>Kelvanbrook is a technology solution provider based in Houston, Texas. Our goal is to make technology a non-issue for individuals and small to medium size businesses ranging from 5 to 150 Users. Kelvanbrook has the experience, the tools, high-level technology solutions and training to power your business and your work force. We understand that all business's have one goal in common!</p>
    <ul><li>&gt; Disaster Recovery</li><li>&gt; Audio/Video Multimedia.</li></ul>
    <a class="btn">Read More</a>
  </div>
</section>
<div class="flex-photo" style="position:absolute" role="img" aria-label="Photo of a technician working on a laptop beside server racks"></div>

<section class="quote">
  <div class="quote-photo" role="img" aria-label="Photo of three businessmen smiling around a laptop"></div>
  <p class="quote-text">"Let us worry about your technology..."<br>" So you don't have to!"</p>
</section>

<section class="testimonials">
  <h2>Testimonial</h2>
  <div class="t-row">
    <div class="t-card" style="left:90px"><div class="t-avatar" role="img" aria-label="Portrait photo of a client"></div><h3><b>Name,</b> Director</h3><p>"Lorem ipsum dolor amet conse ctetur<br>dolore elit,sed do eiusmod tempor<br>et dolore magna."</p><div class="role">Lorem ipsum dolor</div><a class="more">read more... <svg width="18" height="18" viewBox="0 0 20 20"><circle cx="10" cy="10" r="8.5" fill="none" stroke="#2b2b2b" stroke-width="2"/><path d="M6 10h7M10 6.5l3.5 3.5-3.5 3.5" fill="none" stroke="#2b2b2b" stroke-width="2"/></svg></a></div>
    <div class="t-card" style="left:443px"><div class="t-avatar" role="img" aria-label="Portrait photo of a client"></div><h3><b>Name,</b> Director</h3><p>"Lorem ipsum dolor amet conse ctetur<br>dolore elit,sed do eiusmod tempor<br>et dolore magna."</p><div class="role">Lorem ipsum dolor</div><a class="more">read more... <svg width="18" height="18" viewBox="0 0 20 20"><circle cx="10" cy="10" r="8.5" fill="none" stroke="#2b2b2b" stroke-width="2"/><path d="M6 10h7M10 6.5l3.5 3.5-3.5 3.5" fill="none" stroke="#2b2b2b" stroke-width="2"/></svg></a></div>
    <div class="t-card" style="left:818px"><div class="t-avatar" role="img" aria-label="Portrait photo of a client"></div><h3><b>Name,</b> Director</h3><p>"Lorem ipsum dolor amet conse ctetur<br>dolore elit,sed do eiusmod tempor<br>et dolore magna."</p><div class="role">Lorem ipsum dolor</div><a class="more">read more... <svg width="18" height="18" viewBox="0 0 20 20"><circle cx="10" cy="10" r="8.5" fill="none" stroke="#2b2b2b" stroke-width="2"/><path d="M6 10h7M10 6.5l3.5 3.5-3.5 3.5" fill="none" stroke="#2b2b2b" stroke-width="2"/></svg></a></div>
  </div>
</section>

<section class="newsletter">
  <h2>Subscribe to our newsletter</h2>
  <h3>To receive the latest news &amp; update</h3>
  <div class="news-form"><span>Your E-Mail</span><b>Submit</b></div>
</section>

<footer class="site-footer">
  <h2>Get in touch with us</h2>
  <div class="foot-links">About | Contact | Support | Clients | Careers</div>
  <div class="foot-contact">
    <div class="foot-item"><i><svg width="22" height="30" viewBox="0 0 20 26"><path d="M10 1C5 1 1 5 1 9.8 1 16.5 10 25 10 25s9-8.5 9-15.2C19 5 15 1 10 1z" fill="none" stroke="#fff" stroke-width="2"/><circle cx="10" cy="9.5" r="3.2" fill="none" stroke="#fff" stroke-width="2"/></svg></i>123 Street, City Name, DC 12345</div>
    <div class="foot-item"><i><svg width="20" height="30" viewBox="0 0 20 30"><rect x="1" y="1" width="18" height="28" rx="3" fill="none" stroke="#fff" stroke-width="2"/><path d="M7 24h6" stroke="#fff" stroke-width="2"/></svg></i>1 234 567 890</div>
    <div class="foot-item"><i><svg width="30" height="30" viewBox="0 0 30 30"><circle cx="15" cy="15" r="14" fill="#fff"/><rect x="7" y="10" width="16" height="11" fill="none" stroke="#3d3d3d" stroke-width="2"/><path d="M7 10l8 6 8-6" fill="none" stroke="#3d3d3d" stroke-width="2"/></svg></i>info@kelvanbrook.com</div>
  </div>
  <div class="social-foot"><i></i><i></i><i></i><i></i><i></i></div>
</footer>

<div class="copyright" style="position:absolute;left:0;width:1200px">Copyright © 2007 - Kelvanbrook Development Group, Inc - All rights reserved</div>

</body>
</html>
```